Moxy Fen needs some awesome stationary

Do you have what it takes to get my brand? You either do or you don't, have a crack at a design and you my just win my business.

I don't want to waste your or my time, so put your creative genius on either a business card or envelope.

I however need a package of stationary that follows the same brand. I will message you to complete the remaining should I like your first submission.

Here is what I need, have a go!

Basically I need the following for my small business based in melbourne.
- Letterhead (printer ready and MS Word)
- Business Card
- Compliments Slip
- Envelope
- Proposal Cover Page (MS Word only)
- Presentation Folder
- Marbled Fox Cards
- Student Name Tent
- Index Cards
- Vell-Ka

I am establishing the brand and it must be modern, professional but also relaxed; that is not formal and not corporate. It represents a company are leaders, but small enough to care and operate like a bunch of friends. We are bringing people and conversations back to business, and turfing out all the bureaucracy and crazy and wasteful procedures. Its about "lets talk and figure it out together and find even better ways".

Target Market(s)

Mainly companies that build software products, but Agile practices are used in many other industries (even graphic design projects)

Industry/Entity Type

Information Technology

Font styles to use
Sans Serif

Colors
3176b5
aaaaaa

Requirements
Must have
• I like curves and circles and not boxes or rectangles.
• I want a colour rich design with my brand colours, but it must be balanced.
• I want more modern than traditional, but simple modern
Should not have
• Not corporate
• Please don't waste my time if your not going to think about it.
• Don't mess with my primary logo
• Don't change my colours
• Don't overlay logo on image

```html
<!DOCTYPE html>
<html lang="en">
<head>
<meta charset="utf-8">
<title>Moxy Fen — Business Card</title>
<link href="https://fonts.googleapis.com/css2?family=Questrial&family=PT+Sans+Narrow:wght@400;700&display=swap" rel="stylesheet">
<style>
  :root {
    --brand-blue: #3176b5;
    --brand-blue-deep: #1c55a8;
    --brand-blue-light: #2f7ccc;
    --brand-grey: #aaaaaa;
    --ink: #3c3c3c;
    --paper: #ffffff;
    --backdrop: #c5d5e4;
  }
  * { margin: 0; padding: 0; box-sizing: border-box; }
  html, body { width: 1200px; height: 800px; overflow: hidden; }
  body {
    background: var(--backdrop);
    font-family: "PT Sans Narrow", sans-serif;
    position: relative;
  }
  .card {
    position: absolute;
    top: 247px;
    width: 500px;
    height: 306px;
    box-shadow: 0 6px 18px rgba(30, 60, 100, 0.18);
    overflow: hidden;
  }
  .card--front { left: 70px; background: var(--brand-blue-deep); }
  .card--back { left: 630px; background: var(--paper); }

  .front__pattern {
    position: absolute; inset: 0;
    background: radial-gradient(ellipse at 55% 40%, var(--brand-blue-light) 0%, var(--brand-blue-deep) 75%);
  }
  .front__brand {
    position: absolute; left: 0; right: 0; top: 92px;
    display: flex; flex-direction: column; align-items: center;
    color: var(--paper);
  }
  .front__brand-row { display: flex; align-items: center; gap: 14px; }
  .front__dot { width: 34px; height: 34px; border-radius: 50%; background: var(--paper); }
  .front__name { font-family: "Questrial", sans-serif; font-size: 48px; line-height: 1; }
  .front__url { font-family: "Questrial", sans-serif; font-size: 17px; margin-top: 12px; letter-spacing: 0.5px; }

  .back__logo {
    position: absolute; left: 36px; top: 118px; width: 200px;
  }
  .back__logo-row { display: flex; align-items: center; gap: 10px; }
  .back__dot { width: 26px; height: 26px; border-radius: 50%; background: var(--brand-grey); }
  .back__name { font-family: "Questrial", sans-serif; font-size: 36px; color: var(--brand-blue); line-height: 1; }
  .back__rule { height: 1px; background: var(--brand-grey); margin: 8px 0 6px; }
  .back__company { font-family: "Questrial", sans-serif; font-size: 16px; color: var(--brand-blue); }

  .back__divider {
    position: absolute; left: 258px; top: 40px; width: 1px; height: 226px;
    background: linear-gradient(var(--paper), #d4d4d4 30%, #d4d4d4 70%, var(--paper));
  }
  .contact { position: absolute; left: 278px; top: 58px; color: var(--ink); }
  .contact__person {
    font-family: "Questrial", sans-serif; font-size: 18px; letter-spacing: 2px;
    text-transform: uppercase; color: var(--brand-blue-deep);
  }
  .contact__title { font-size: 11px; color: #666; margin: 2px 0 14px; }
  .contact__list { list-style: none; font-size: 15px; line-height: 1.3; }
  .contact__item { display: flex; gap: 8px; margin-bottom: 7px; }
  .contact__icon { width: 16px; height: 16px; flex: none; margin-top: 1px; }
  .contact__strong { font-weight: 700; }
</style>
</head>
<body>
  <section class="card card--front" aria-label="Business card front">
    <div class="front__pattern" role="img" aria-label="Blue background with a subtle repeating swirl pattern"></div>
    <div class="front__brand">
      <div class="front__brand-row">
        <span class="front__dot"></span>
        <span class="front__name">Moxy Fen</span>
      </div>
      <span class="front__url">www.moxy-fen.com.au</span>
    </div>
  </section>

  <section class="card card--back" aria-label="Business card back">
    <div class="back__logo">
      <div class="back__logo-row">
        <span class="back__dot"></span>
        <span class="back__name">Moxy Fen</span>
      </div>
      <div class="back__rule"></div>
      <div class="back__company">Moxy Fen Pty Ltd</div>
    </div>

    <div class="back__divider"></div>

    <div class="contact">
      <div class="contact__person">Jordan Keble</div>
      <div class="contact__title">CEO, Professional Scrum Trainer</div>
      <ul class="contact__list">
        <li class="contact__item">
          <svg class="contact__icon" viewBox="0 0 16 16" aria-hidden="true"><circle cx="8" cy="8" r="7.3" fill="none" stroke="#3176b5"/><path d="M8 3.5a2.7 2.7 0 0 1 2.7 2.7C10.7 8.3 8 12 8 12S5.3 8.3 5.3 6.2A2.7 2.7 0 0 1 8 3.5z" fill="#3176b5"/><circle cx="8" cy="6.2" r="1" fill="#fff"/></svg>
          <span>PO Box 4410, Larkfield North,<br>VIC 3190, Australia</span>
        </li>
        <li class="contact__item">
          <svg class="contact__icon" viewBox="0 0 16 16" aria-hidden="true"><circle cx="8" cy="8" r="7.3" fill="none" stroke="#3176b5"/><path d="M5.3 4.3l1.5-.3.9 2-1 .8a5 5 0 0 0 2.5 2.5l.8-1 2 .9-.3 1.5C9 11 5 7 5.3 4.3z" fill="#3176b5"/></svg>
          <span><span class="contact__strong">1300MOXYF</span><br>+61 400 123 987</span>
        </li>
        <li class="contact__item">
          <svg class="contact__icon" viewBox="0 0 16 16" aria-hidden="true"><circle cx="8" cy="8" r="7.3" fill="none" stroke="#3176b5"/><rect x="4" y="5.2" width="8" height="5.6" fill="none" stroke="#3176b5"/><path d="M4 5.2l4 3 4-3" fill="none" stroke="#3176b5"/></svg>
          <span>jordan@moxy-fen.com.au</span>
        </li>
      </ul>
    </div>
  </section>
</body>
</html>
```